Luxury Toilet Rental Business. Tallowby Hire.

Tallowby Hire (the logo is in the uploaded files)
We RENT and SELL Luxury Trailer toilets.
- Show location, number, pricing, pictures.
- We have two stall trailers for rent AND 3 stall trailers
- We sell them too
- We want our phone number shown
- We are a local company
- Slogan: Brighten your gathering with Tallowby Hire. The Velvet Privy
- We want a pricing portion
- We want the sizes shown
- We want the different rates/ prices shown
- We do 1 day rentals
- We do 1 week rentals
- We want the service area. We serve Los Angeles County, Orange County, Riverside County, San Bernardino County, and Palm Desert.
- Our location is in Santa Ana California

Target Market(s)

Event planners, wedding planners, venue planners, concerts, events, gatherings.

Industry/Entity Type

Luxury Toilet Rentals

Number of Pages Required

1 page

Font styles to use
Serif
Sans Serif

Colors
EE7325
F08F49
F5BC92
FAE3D3
FDF4ED

Requirements
Must have
• Location, pricing, pictures, available areas. Our slogan.
Nice to have
• I like the idea of having tabs that show price, a tab that shows our contact information, pictures, event ideas, and where we service (the areas we'll go to)

```html
<!DOCTYPE html>
<html lang="en">
<head>
<meta charset="utf-8">
<title>Tallowby Hire — Luxury Trailer Toilets</title>
<link href="https://fonts.googleapis.com/css2?family=Unbounded:wght@700;800&family=Roboto:wght@400;500;700&display=swap" rel="stylesheet">
<style>
:root{
  --orange:#ee7325;
  --orange-2:#f08f49;
  --peach:#f5bc92;
  --cream:#fae3d3;
  --ivory:#fdf4ed;
  --ink:#1d1d1d;
  --text:#555;
  --grey-bg:#f3f3f3;
  --line:#d9d9d9;
  --white:#fff;
}
*{box-sizing:border-box;margin:0;padding:0}
html,body{width:1200px;height:4898px;overflow:hidden;background:var(--white)}
body{font-family:"Roboto",Arial,sans-serif;color:var(--ink)}
.page{position:relative;width:1200px;height:4898px;overflow:hidden}
.abs{position:absolute}
.display{font-family:"Unbounded","Arial Black",sans-serif;font-weight:800;text-transform:uppercase;letter-spacing:-0.5px}
.rule{position:absolute;height:3px;width:48px;background:var(--orange)}
.arrow-box{display:inline-flex;align-items:center;justify-content:center;width:26px;height:26px;background:var(--orange)}
.arrow-box svg{width:14px;height:14px}

/* header */
.site-header{position:absolute;top:0;left:0;width:1200px;height:76px;background:var(--white);border-bottom:1px solid #eee}
.brand{position:absolute;left:114px;top:22px;display:flex;align-items:center;gap:10px}
.brand-square{width:26px;height:26px;background:var(--orange)}
.brand-name{font-family:"Unbounded",sans-serif;font-weight:800;font-size:20px;color:var(--ink);text-transform:uppercase}
.nav a{position:absolute;top:31px;font-size:13px;font-weight:500;color:#333;text-decoration:none;text-transform:uppercase}
.nav a.active{color:var(--orange)}
.nav a.active::before{content:"";position:absolute;left:0;right:0;top:-9px;height:2px;background:var(--orange)}
.call{position:absolute;left:924px;top:15px;width:162px;height:46px;border:2px solid #333;display:flex;align-items:center;gap:10px;padding-left:10px;font-size:13px;font-weight:500}

/* hero */
.hero{position:absolute;top:76px;left:0;width:1200px;height:643px;background:linear-gradient(180deg,#6d6f70 0%,#55585a 40%,#3e4142 75%,#2f3132 100%)}
.hero-panel{position:absolute;left:110px;top:224px;width:474px;height:210px;background:rgba(20,20,20,.55)}
.hero h1{position:absolute;left:112px;top:244px;font-size:33px;line-height:35px;color:var(--white)}
.hero .tagline{position:absolute;left:112px;top:352px;font-family:"Unbounded",sans-serif;font-weight:800;font-size:15px;color:var(--orange);text-transform:uppercase}
.btn-light{position:absolute;left:114px;top:388px;width:162px;height:40px;background:var(--white);display:flex;align-items:center;justify-content:space-between;padding:0 8px 0 20px;font-size:12px;font-weight:500;text-transform:uppercase}
.play{position:absolute;left:807px;top:285px;width:72px;height:72px;border-radius:50%;background:var(--orange);box-shadow:0 0 0 10px rgba(238,115,37,.3);display:flex;align-items:center;justify-content:center}

/* about */
.about{position:absolute;top:719px;left:0;width:1200px;height:660px}
.about-photo-a{position:absolute;left:110px;top:86px;width:223px;height:405px;background:linear-gradient(180deg,#8a8d8f,#5e6163 60%,#4a4c4d)}
.about-photo-b{position:absolute;left:352px;top:139px;width:221px;height:403px;background:linear-gradient(180deg,#c9571c,#b24a15 60%,#8e3b12)}
.about-badge{position:absolute;left:266px;top:228px;width:152px;height:152px;border-radius:50%;background:var(--white);border:8px solid var(--orange);display:flex;align-items:center;justify-content:center;font-family:"Unbounded",sans-serif;font-weight:800;font-size:17px;color:var(--orange);text-transform:uppercase}
.about h2{position:absolute;left:622px;top:99px;font-size:30px}
.about h2 span{color:var(--orange)}
.about p{position:absolute;left:622px;width:466px;font-size:13.3px;line-height:21.5px;color:var(--text);text-align:justify}
.btn-outline{position:absolute;display:flex;align-items:center;justify-content:space-between;border:2px solid #333;padding:0 8px 0 14px;font-size:12px;font-weight:500;text-transform:uppercase;background:var(--white)}

/* trailers */
.trailers{position:absolute;top:1379px;left:0;width:1200px;height:789px;background:var(--grey-bg)}
.section-title{position:absolute;left:0;width:1200px;text-align:center;font-size:30px}
.card{position:absolute;top:177px;width:470px;height:496px;background:var(--white);box-shadow:0 2px 12px rgba(0,0,0,.06)}
.card-img{position:absolute;left:15px;top:13px;width:440px;height:247px}
.card h3{position:absolute;left:26px;top:282px;font-size:16px;font-weight:500;text-transform:uppercase}
.card .desc{position:absolute;left:26px;top:307px;width:420px;font-size:12.5px;line-height:21px;color:var(--text)}
.card .was{position:absolute;left:26px;top:361px;font-size:13px;color:#999;text-decoration:line-through}
.card .price{position:absolute;left:26px;top:381px;font-size:25px;font-weight:500;color:var(--orange)}
.card .spec{position:absolute;left:147px;font-size:11.5px;color:var(--text);display:flex;align-items:center;gap:14px}
.card .btn-outline{top:610px}
.slider-arrow{position:absolute;top:1790px}

/* service */
.service{position:absolute;top:2168px;left:0;width:1200px;height:556px}
.service-band{position:absolute;left:0;top:0;width:491px;height:556px;background:var(--orange)}
.service h2{position:absolute;left:110px;top:76px;font-size:31px;line-height:34px;color:var(--white)}
.service .rule{left:110px;top:158px;background:var(--white)}
.mini-arrow{position:absolute;top:124px;width:30px;height:30px;border:1px solid #bbb;background:var(--white);display:flex;align-items:center;justify-content:center}
.area{position:absolute;top:184px;width:210px;height:273px;background:var(--white);box-shadow:0 2px 8px rgba(0,0,0,.08)}
.area-img{height:223px}
.area span{display:block;text-align:center;font-size:13.5px;font-weight:500;line-height:50px}

/* gallery */
.gallery{position:absolute;top:2724px;left:0;width:1200px;height:760px}
.tile{position:absolute}
.zoom{position:absolute;left:570px;top:263px;width:58px;height:58px;border-radius:50%;background:var(--white);display:flex;align-items:center;justify-content:center;font-size:18px;color:#555}

/* location */
.location{position:absolute;top:3519px;left:0;width:1200px;height:646px}
.location-band{position:absolute;left:599px;top:0;width:601px;height:500px;background:var(--orange)}
.location h2{position:absolute;left:671px;top:62px;font-size:30px;color:var(--white)}
.location .rule{left:671px;top:106px;background:var(--white)}
.location-photo{position:absolute;left:0;top:148px;width:1090px;height:498px;background:linear-gradient(180deg,#c7b49a 0%,#8e7a66 30%,#4e4a44 65%,#2f2e2c 100%)}
.city{position:absolute;left:0;top:325px;width:1090px;text-align:center;font-size:64px;line-height:72px;color:var(--white);letter-spacing:1px}

/* contact */
.contact{position:absolute;top:4165px;left:0;width:1200px;height:657px}
.contact h2{position:absolute;left:110px;top:98px;font-size:23px}
.contact .lead{position:absolute;left:110px;top:146px;font-size:20px;color:#444}
.contact .pitch{position:absolute;left:110px;top:196px;font-size:18px;line-height:30px;font-weight:500;text-transform:uppercase}
.info-icon{position:absolute;left:110px;width:58px;height:58px;border-radius:50%;background:var(--white);box-shadow:0 2px 10px rgba(0,0,0,.12);display:flex;align-items:center;justify-content:center}
.info-text{position:absolute;left:196px;font-size:20px;line-height:31px;color:#444}
.form-card{position:absolute;left:601px;top:95px;width:487px;height:502px;background:var(--white);box-shadow:0 4px 24px rgba(0,0,0,.08)}
.field{position:absolute;left:29px;width:428px;height:54px;border:1px solid var(--line);border-radius:27px;padding:18px 28px;font-size:13px;color:#666}
.field.message{height:152px;border-radius:30px}
.submit{position:absolute;left:29px;top:417px;width:156px;height:49px;border-radius:25px;background:var(--orange);color:var(--white);font-size:13px;font-weight:700;display:flex;align-items:center;justify-content:center;text-transform:uppercase}

/* footer */
.site-footer{position:absolute;top:4822px;left:0;width:1200px;height:76px;background:#111}
.social{position:absolute;top:18px;width:42px;height:42px;border-radius:50%;border:1px solid #aaa}
.copyright{position:absolute;right:110px;top:30px;font-size:13px;color:#ddd}
</style>
</head>
<body>
<div class="page">

  <header class="site-header">
    <div class="brand"><span class="brand-square"></span><span class="brand-name">Tallowby Hire</span></div>
    <nav class="nav">
      <a class="active" style="left:389px">Home</a>
      <a style="left:456px">Events</a>
      <a style="left:535px">Services Area</a>
      <a style="left:668px">Gallery</a>
      <a style="left:757px">Pricing</a>
      <a style="left:839px">Contact</a>
    </nav>
    <div class="call">
      <span class="arrow-box"><svg viewBox="0 0 24 24" fill="#fff"><path d="M6.6 10.8a15 15 0 0 0 6.6 6.6l2.2-2.2c.3-.3.7-.4 1-.2 1.1.4 2.3.6 3.6.6.6 0 1 .4 1 1V20c0 .6-.4 1-1 1A17 17 0 0 1 3 4c0-.6.4-1 1-1h3.5c.6 0 1 .4 1 1 0 1.3.2 2.5.6 3.6.1.3 0 .7-.2 1z"/></svg></span>
      +1 555 014 2290
    </div>
  </header>

  <section class="hero" role="img" aria-label="Photo of a grey two-stall luxury restroom trailer with blue steps parked outside a warehouse">
    <div class="hero-panel"></div>
    <h1 class="display">Brighten your<br>gathering with<br>Tallowby Hire.</h1>
    <div class="tagline">The Velvet Privy</div>
    <div class="btn-light">Get Started <span class="arrow-box"><svg viewBox="0 0 16 16"><path d="M3 8h9M8 4l4 4-4 4" stroke="#fff" stroke-width="2" fill="none"/></svg></span></div>
    <div class="play"><svg width="22" height="22" viewBox="0 0 22 22"><path d="M6 3l13 8-13 8z" fill="#fff"/></svg></div>
  </section>

  <section class="about">
    <div class="about-photo-a" role="img" aria-label="Photo of a restroom trailer with its door open"></div>
    <div class="about-photo-b" role="img" aria-label="Orange-tinted photo of a restroom trailer in a yard"></div>
    <div class="about-badge">Tallowby</div>
    <h2 class="display">About <span>Us</span></h2>
    <div class="rule" style="left:622px;top:148px"></div>
    <p style="top:165px">Lorem ipsum dolor sit amet, consectetur adipiscing elit, sed do eiusmod tempor incididunt ut labore et dolore magna aliqua. Ut enim ad minim veniam, quis nostrud exercitation ullamco laboris nisi ut aliquip ex ea commodo consequat. Duis aute irure dolor in reprehenderit in voluptate velit esse cillum dolore eu fugiat nulla pariatur.</p>
    <p style="top:295px">Excepteur sint occaecat cupidatat non proident, sunt in culpa qui officia deserunt mollit anim id est laborum. Lorem ipsum dolor sit amet, consectetur adipiscing elit, sed do eiusmod tempor incididunt ut labore et dolore magna aliqua. Ut enim ad minim veniam, quis nostrud exercitation ullamco laboris nisi ut aliquip ex ea commodo consequat. Duis aute irure dolor in reprehenderit in voluptate velit esse cillum dolore eu fugiat nulla pariatur. Excepteur sint occaecat cupidatat non proident, sunt in culpa qui officia deserunt mollit anim id est laborum.</p>
    <div class="btn-outline" style="left:622px;top:481px;width:165px;height:46px">Read More <span class="arrow-box"><svg viewBox="0 0 16 16"><path d="M3 8h9M8 4l4 4-4 4" stroke="#fff" stroke-width="2" fill="none"/></svg></span></div>
  </section>

  <section class="trailers">
    <h2 class="display section-title" style="top:90px">Luxury Trailer Toilets</h2>
    <div class="rule" style="left:576px;top:141px"></div>

    <article class="card" style="left:110px">
      <div class="card-img" role="img" aria-label="Photo of a two-stall grey restroom trailer" style="background:linear-gradient(180deg,#a8a59b,#7e7f7d 55%,#9a9a98)"></div>
      <h3>Two Stall Trailers</h3>
      <p class="desc">Lorem ipsum dolor sit amet, consectetur adipiscing elit Lorem ipsum dolor sit amet, consectetur adipiscing elit</p>
      <div class="was">$75.00</div>
      <div class="price">$50.00</div>
      <div class="spec" style="top:363px"><svg width="12" height="13" viewBox="0 0 12 13" fill="#ee7325"><circle cx="6" cy="3.5" r="3"/><path d="M0 13c0-4 2.5-6 6-6s6 2 6 6z"/></svg>Up to 200 Guests</div>
      <div class="spec" style="top:388px"><svg width="12" height="13" viewBox="0 0 12 13" fill="none" stroke="#ee7325" stroke-width="1.5"><path d="M6 1v6M1 12l5-5 5 5M1 12h10" stroke-dasharray="2 1.5"/></svg>19 ft long by 10 ft wide</div>
      <div class="btn-outline" style="left:27px;top:433px;width:163px;height:42px">1 Day Rentals <span class="arrow-box"><svg viewBox="0 0 16 16"><path d="M3 8h9M8 4l4 4-4 4" stroke="#fff" stroke-width="2" fill="none"/></svg></span></div>
      <div class="btn-outline" style="left:208px;top:433px;width:173px;height:42px">1 Week Rentals <span class="arrow-box"><svg viewBox="0 0 16 16"><path d="M3 8h9M8 4l4 4-4 4" stroke="#fff" stroke-width="2" fill="none"/></svg></span></div>
    </article>

    <article class="card" style="left:618px">
      <div class="card-img" role="img" aria-label="Photo of a three-stall white restroom trailer at an outdoor event" style="background:linear-gradient(180deg,#3d8fd6 0%,#8cc0e8 45%,#d8d8d4 60%,#4f7a3a 100%)"></div>
      <h3>Three Stall Trailers</h3>
      <p class="desc">Lorem ipsum dolor sit amet, consectetur adipiscing elit Lorem ipsum dolor sit amet, consectetur adipiscing elit</p>
      <div class="was">$100.00</div>
      <div class="price">$75.00</div>
      <div class="spec" style="top:363px"><svg width="12" height="13" viewBox="0 0 12 13" fill="#ee7325"><circle cx="6" cy="3.5" r="3"/><path d="M0 13c0-4 2.5-6 6-6s6 2 6 6z"/></svg>Up to 300 Guests</div>
      <div class="spec" style="top:388px"><svg width="12" height="13" viewBox="0 0 12 13" fill="none" stroke="#ee7325" stroke-width="1.5"><path d="M6 1v6M1 12l5-5 5 5M1 12h10" stroke-dasharray="2 1.5"/></svg>19 ft long by 10 ft wide</div>
      <div class="btn-outline" style="left:27px;top:433px;width:163px;height:42px">1 Day Rentals <span class="arrow-box"><svg viewBox="0 0 16 16"><path d="M3 8h9M8 4l4 4-4 4" stroke="#fff" stroke-width="2" fill="none"/></svg></span></div>
      <div class="btn-outline" style="left:208px;top:433px;width:173px;height:42px">1 Week Rentals <span class="arrow-box"><svg viewBox="0 0 16 16"><path d="M3 8h9M8 4l4 4-4 4" stroke="#fff" stroke-width="2" fill="none"/></svg></span></div>
    </article>

    <svg class="abs" style="left:38px;top:409px" width="38" height="66" viewBox="0 0 38 66"><path d="M34 2L4 33l30 31" stroke="#111" stroke-width="3" fill="none"/></svg>
    <svg class="abs" style="left:1124px;top:409px" width="38" height="66" viewBox="0 0 38 66"><path d="M4 2l30 31L4 64" stroke="#111" stroke-width="3" fill="none"/></svg>
  </section>

  <section class="service">
    <div class="service-band"></div>
    <h2 class="display">Where<br>We Service</h2>
    <div class="rule"></div>
    <div class="mini-arrow" style="left:1017px"><svg width="8" height="10" viewBox="0 0 8 10"><path d="M6 1L2 5l4 4" stroke="#333" fill="none"/></svg></div>
    <div class="mini-arrow" style="left:1058px"><svg width="8" height="10" viewBox="0 0 8 10"><path d="M2 1l4 4-4 4" stroke="#333" fill="none"/></svg></div>

    <div class="area" style="left:110px"><div class="area-img" role="img" aria-label="Photo of the Los Angeles skyline" style="background:linear-gradient(180deg,#4f8fd0,#8fb7d9 50%,#5b6b6e)"></div><span>Los Angeles County</span></div>
    <div class="area" style="left:329px"><div class="area-img" role="img" aria-label="Photo of an Orange County coastline at sunset" style="background:linear-gradient(180deg,#d9b999,#a8988a 45%,#6a7870)"></div><span>Orange County</span></div>
    <div class="area" style="left:548px"><div class="area-img" role="img" aria-label="Photo of a rocky coastal cove at dusk" style="background:linear-gradient(180deg,#6c8fc4,#d89b6e 45%,#4d6270)"></div><span>Riverside County</span></div>
    <div class="area" style="left:767px"><div class="area-img" role="img" aria-label="Aerial photo of a San Bernardino neighbourhood" style="background:linear-gradient(180deg,#6b7d55,#9b8c7e 50%,#59704a)"></div><span>San Bernardino County</span></div>
    <div class="area" style="left:985px"><div class="area-img" role="img" aria-label="Photo of desert rocks and Joshua trees near Palm Desert" style="background:linear-gradient(180deg,#4c84c9,#9cbde0 40%,#c28a56 75%,#8b6a48)"></div><span>Palm Desert</span></div>
  </section>

  <section class="gallery">
    <h2 class="display section-title" style="top:94px">Our Gallery</h2>
    <div class="rule" style="left:576px;top:140px"></div>
    <div class="tile" role="img" aria-label="Photo of a trailer restroom interior with toilet and vanity" style="left:110px;top:176px;width:308px;height:232px;background:linear-gradient(180deg,#e6e6e4,#cfcfcc 70%,#c3ad8c)"></div>
    <div class="tile" role="img" aria-label="Photo of a white sink vanity beside a toilet" style="left:445px;top:176px;width:308px;height:232px;background:linear-gradient(180deg,#dcdcda,#f1f1f0 60%,#bfae93)"></div>
    <div class="zoom">+</div>
    <div class="tile" role="img" aria-label="Photo of a compact restroom with sink and toilet" style="left:780px;top:176px;width:308px;height:232px;background:linear-gradient(180deg,#ebebea,#d6d6d4 70%,#c7b597)"></div>
    <div class="tile" role="img" aria-label="Photo looking down at a restroom sink and toilet" style="left:110px;top:435px;width:478px;height:230px;background:linear-gradient(180deg,#e4e4e2,#cdccc9 65%,#b8a689)"></div>
    <div class="tile" role="img" aria-label="Photo of a grey restroom trailer outside a warehouse" style="left:610px;top:435px;width:478px;height:230px;background:linear-gradient(180deg,#a6a399,#777a7a 55%,#8f8f8d)"></div>
  </section>

  <section class="location">
    <div class="location-band"></div>
    <h2 class="display">Our Location</h2>
    <div class="rule"></div>
    <div class="location-photo" role="img" aria-label="Aerial photo of Santa Ana at sunset with palm-lined streets"></div>
    <div class="display city">Santa Ana<br>California</div>
  </section>

  <section class="contact">
    <h2 class="display">Ready to get in touch?</h2>
    <p class="lead">Contact us to discuss your property goals</p>
    <p class="pitch">Contact us to speak with an agent<br>or request an appraisal</p>

    <div class="info-icon" style="top:279px"><svg width="18" height="14" viewBox="0 0 18 14" fill="#ee7325"><path d="M0 0h18v2L9 8 0 2z"/><path d="M0 4l9 6 9-6v10H0z"/></svg></div>
    <div class="info-text" style="top:283px">Email:<br>hello@tallowbyhire.com</div>
    <div class="info-icon" style="top:365px"><svg width="17" height="17" viewBox="0 0 24 24" fill="#ee7325"><path d="M6.6 10.8a15 15 0 0 0 6.6 6.6l2.2-2.2c.3-.3.7-.4 1-.2 1.1.4 2.3.6 3.6.6.6 0 1 .4 1 1V20c0 .6-.4 1-1 1A17 17 0 0 1 3 4c0-.6.4-1 1-1h3.5c.6 0 1 .4 1 1 0 1.3.2 2.5.6 3.6.1.3 0 .7-.2 1z"/></svg></div>
    <div class="info-text" style="top:373px">Tel:<br>+1 555 014 2290</div>
    <div class="info-icon" style="top:451px"><svg width="14" height="19" viewBox="0 0 14 19" fill="#ee7325"><path d="M7 0a7 7 0 0 1 7 7c0 5-7 12-7 12S0 12 0 7a7 7 0 0 1 7-7zm0 4a3 3 0 1 0 0 6 3 3 0 0 0 0-6z"/></svg></div>
    <div class="info-text" style="top:464px">Santa Ana California</div>

    <form class="form-card">
      <div class="field" style="top:31px">Name</div>
      <div class="field" style="top:105px">Email</div>
      <div class="field" style="top:177px">Subject</div>
      <div class="field message" style="top:250px">Add a message</div>
      <div class="submit">Submit Now</div>
    </form>
  </section>

  <footer class="site-footer">
    <span class="social" style="left:108px"></span>
    <span class="social" style="left:156px"></span>
    <span class="social" style="left:203px"></span>
    <div class="copyright">© Copyrights 2024 | All Rights Reserved</div>
  </footer>

</div>
</body>
</html>
```